A clean crisp business card for a Landscape Construction company. Designed to be easy to read contact/ info and also be appealing/interesting, unlike a traditional business card.

Industry/Entity Type

Landscape Construction

Contact Information for Business Card

Company name : Brambleford Landscape Construction, phone number: (877) 62Vista, website:Bramblefordyards.example, Email, sales@bramblefordyards.example

Requirements
Nice to have
• Luxurious finishes/ details…. Icons or emblems next to contact info
Should not have
• Clipart or general pictures

```html
<!DOCTYPE html>
<html lang="en">
<head>
<meta charset="utf-8">
<title>Brambleford Landscape Construction – Business Card</title>
<link rel="stylesheet" href="https://fonts.googleapis.com/css2?family=Cinzel:wght@600&family=Arimo:wght@400;700&display=swap">
<style>
  :root {
    --card-blue: #2270bd;
    --deep-blue: #1b5fa8;
    --leaf-green: #9bca3c;
    --paper: #ffffff;
    --backdrop: #2a2a2c;
  }
  html, body {
    margin: 0;
    width: 1200px;
    height: 900px;
    overflow: hidden;
    background: var(--backdrop);
  }
  .canvas {
    position: relative;
    width: 1200px;
    height: 900px;
  }
  .card {
    position: absolute;
    left: 250px;
    width: 700px;
    height: 400px;
    border-radius: 22px;
    overflow: hidden;
    box-shadow: 0 10px 30px rgba(0,0,0,0.5);
  }
  .card-front {
    top: 40px;
    background: var(--card-blue);
    display: flex;
    flex-direction: column;
    align-items: center;
    justify-content: center;
  }
  .brand-name {
    font-family: "Cinzel", serif;
    font-weight: 600;
    color: var(--paper);
    text-align: center;
    line-height: 1.1;
    margin: 0;
  }
  .brand-name .brand-main {
    display: block;
    font-size: 60px;
    letter-spacing: 1px;
  }
  .brand-name .brand-sub {
    display: block;
    font-size: 19px;
    letter-spacing: 6px;
    margin-top: 6px;
  }
  .card-back {
    top: 470px;
    background: var(--card-blue);
  }
  .accent-band {
    position: absolute;
    left: 0;
    right: 0;
    bottom: 0;
    height: 118px;
    background: linear-gradient(180deg, #ffffff 0%, #f1f6fb 100%);
    border-top: 7px solid var(--leaf-green);
  }
  .contact {
    position: absolute;
    left: 40px;
    top: 44px;
    font-family: "Arimo", sans-serif;
    color: var(--paper);
  }
  .contact .person-name {
    margin: 0;
    font-size: 30px;
    font-weight: 700;
    color: var(--leaf-green);
    letter-spacing: 0.5px;
  }
  .contact .person-role {
    margin: 2px 0 18px;
    font-size: 17px;
  }
  .contact address {
    font-style: normal;
    font-size: 17px;
    line-height: 1.3;
    margin-bottom: 18px;
  }
  .contact-list {
    list-style: none;
    padding: 0;
    margin: 0;
    font-size: 17px;
    line-height: 1.45;
  }
  .contact-list li {
    display: flex;
    align-items: center;
    gap: 9px;
  }
  .contact-list svg {
    width: 14px;
    height: 14px;
    fill: var(--leaf-green);
    flex: none;
  }
  .back-brand {
    position: absolute;
    right: 40px;
    bottom: 24px;
    font-family: "Cinzel", serif;
    font-weight: 600;
    color: var(--deep-blue);
    text-align: right;
    line-height: 1.1;
    margin: 0;
  }
  .back-brand .brand-main {
    display: block;
    font-size: 38px;
  }
  .back-brand .brand-sub {
    display: block;
    font-size: 13px;
    letter-spacing: 4px;
    margin-top: 4px;
  }
</style>
</head>
<body>
<main class="canvas">
  <section class="card card-front">
    <h1 class="brand-name">
      <span class="brand-main">BRAMBLEFORD</span>
      <span class="brand-sub">LANDSCAPE CONSTRUCTION</span>
    </h1>
  </section>

  <section class="card card-back">
    <div class="accent-band" role="img" aria-label="Decorative green and blue wave band sweeping across the lower card"></div>

    <div class="contact">
      <h2 class="person-name">OWEN HARTLEY</h2>
      <p class="person-role">Founder</p>
      <address>4120 W. Larkspur Lane<br>Millbrook, ON 48210</address>
      <ul class="contact-list">
        <li>
          <svg viewBox="0 0 24 24"><path d="M6.6 10.8a15.1 15.1 0 0 0 6.6 6.6l2.2-2.2a1 1 0 0 1 1-.25 11.4 11.4 0 0 0 3.6.6 1 1 0 0 1 1 1V20a1 1 0 0 1-1 1A17 17 0 0 1 3 4a1 1 0 0 1 1-1h3.5a1 1 0 0 1 1 1c0 1.25.2 2.45.6 3.6a1 1 0 0 1-.25 1z"/></svg>
          (877) 62Vista
        </li>
        <li>
          <svg viewBox="0 0 24 24"><path d="M2 5h20v14H2z M2 5l10 8 10-8" stroke="var(--card-blue)" stroke-width="1.5"/></svg>
          sales@bramblefordyards.example
        </li>
        <li>
          <svg viewBox="0 0 24 24"><circle cx="12" cy="12" r="10"/><path d="M2 12h20M12 2c3 3 3 17 0 20M12 2c-3 3-3 17 0 20" stroke="var(--card-blue)" stroke-width="1.5" fill="none"/></svg>
          bramblefordyards.example
        </li>
      </ul>
    </div>

    <p class="back-brand">
      <span class="brand-main">BRAMBLEFORD</span>
      <span class="brand-sub">LANDSCAPE CONSTRUCTION</span>
    </p>
  </section>
</main>
</body>
</html>
```